NZ First of it's kind solutions directory and marketplace for busy Mums needs a business card design

We need a business card design for our new nationwide business in NZ (long term plans to go global). We provide solutions to the everyday challenges that busy Mums face by connecting them with quality communities and suppliers of carefully selected, relevant products and services. We sell direct via our online marketplace. The final design should communicate our values of inclusivity, quality and smart solutions. Colours should incorporate our logo colour palette of #477077 and #6ba8b2. Our website is at https://www.brightnestmums.example

Target Market(s)

busy Mums, Age 28 – 50, female, income over $100K, location main centres NZ primarily but NZ wide. Is likely juggling work or career with a young family. Probably had hobbies which have fallen by the wayside.
-Wants to succeed in her chosen career without compromising on family life
-to successfully juggle her career without feeling like she is compromising her children
- Is time poor, something always has to give and it’s generally her health (she’ll stay up late, get stressed)
- probably ex corporate or professional career. Has discretional income

Industry/Entity Type

Business

Contact Information for Business Card

Lena Forbisher, Founder, BrightNestMums.example (Strapline Tap; Gather; Sorted), 47 Kowhai Terrace, Ellerslie, Auckland 1051, New Zealand. Mob: 021 483 517 Ph: +64 (0)9 571 4860

Font styles to use
Other font styles liked:
• Raleway, and/or Architects Daughter

Colors
00a990
33b8a4
86cfc6
cfeae6

Requirements
Must have
• the above details, streamline. the logo and colours associated with those logos
Should not have
• foil or metallic colours

```html
<!DOCTYPE html>
<html lang="en">
<head>
<meta charset="utf-8">
<title>BrightNestMums – Business Card</title>
<link rel="stylesheet" href="https://fonts.googleapis.com/css2?family=Roboto:wght@400;500;700&display=swap">
<style>
  :root {
    --brand-dark: #477077;
    --brand-wave: #4a7377;
    --brand-light: #6ba8b2;
    --card-paper: #f2f2f2;
    --stage: #2a2a2a;
    --ink-light: #ffffff;
  }
  * { margin: 0; padding: 0; box-sizing: border-box; }
  html, body {
    width: 1200px;
    height: 960px;
    overflow: hidden;
  }
  body {
    background: var(--stage);
    font-family: "Roboto", Arial, sans-serif;
    position: relative;
  }
  .card {
    position: absolute;
    width: 600px;
    height: 343px;
    overflow: hidden;
  }
  .card--front {
    left: 314px;
    top: 113px;
    background: var(--card-paper);
  }
  .card--back {
    left: 311px;
    top: 472px;
    background: var(--brand-light);
  }
  .wave {
    position: absolute;
    inset: 0;
  }
  .brand {
    position: absolute;
    left: 43px;
    top: 66px;
    display: flex;
    align-items: center;
    gap: 12px;
  }
  .brand__dot {
    width: 30px;
    height: 30px;
    border-radius: 50%;
    background: var(--brand-light);
  }
  .brand__name {
    font-size: 31px;
    font-weight: 500;
    color: var(--brand-dark);
    letter-spacing: -0.3px;
  }
  .contact {
    position: absolute;
    right: 24px;
    top: 166px;
    text-align: right;
    color: var(--ink-light);
  }
  .contact__name {
    font-size: 20px;
    font-weight: 500;
    line-height: 24px;
  }
  .contact__role {
    font-size: 15px;
    font-weight: 400;
    line-height: 20px;
    margin-bottom: 12px;
  }
  .contact__line {
    display: flex;
    justify-content: flex-end;
    align-items: center;
    gap: 6px;
    font-size: 14px;
    line-height: 19.5px;
  }
  .contact__icon {
    width: 12px;
    height: 12px;
    flex: none;
  }
  .contact__address {
    margin-top: 8px;
    font-size: 14px;
    line-height: 18px;
  }
  .back-mark {
    position: absolute;
    left: 0;
    right: 0;
    top: 78px;
    display: flex;
    flex-direction: column;
    align-items: center;
    gap: 18px;
  }
  .back-mark__dot {
    width: 110px;
    height: 110px;
    border-radius: 50%;
    background: var(--ink-light);
  }
  .back-mark__name {
    font-size: 26px;
    font-weight: 500;
    color: var(--ink-light);
  }
  .strapline {
    position: absolute;
    left: 0;
    right: 0;
    top: 305px;
    text-align: center;
    font-size: 14px;
    color: var(--ink-light);
  }
</style>
</head>
<body>

  <section class="card card--front">
    <svg class="wave" viewBox="0 0 600 343" width="600" height="343" aria-hidden="true">
      <path d="M0,343 C150,326 240,236 322,172 C414,112 520,112 600,134 L600,343 Z" fill="var(--brand-light)"/>
      <path d="M0,343 C150,332 250,252 332,188 C424,130 522,128 600,143 L600,343 Z" fill="var(--brand-wave)"/>
      <path d="M0,343 C150,332 250,252 332,188 C424,130 522,128 600,143" fill="none" stroke="#ffffff" stroke-width="2"/>
    </svg>

    <div class="brand">
      <span class="brand__dot"></span>
      <span class="brand__name">BrightNestMums</span>
    </div>

    <div class="contact">
      <p class="contact__name">LENA FORBISHER</p>
      <p class="contact__role">FOUNDER</p>
      <p class="contact__line">+64 (0)9 571 4860
        <svg class="contact__icon" viewBox="0 0 12 12" aria-hidden="true">
          <path d="M2.4,0.6 L4.2,2.9 L3.2,4.2 C3.8,5.6 6.4,8.2 7.8,8.8 L9.1,7.8 L11.4,9.6 L10.4,11.2 C6,11.4 0.6,6 0.8,1.6 Z" fill="#fff"/>
        </svg>
      </p>
      <p class="contact__line">021 483 517
        <svg class="contact__icon" viewBox="0 0 12 12" aria-hidden="true">
          <rect x="2.5" y="0.5" width="7" height="11" rx="1" fill="none" stroke="#fff" stroke-width="1.2"/>
          <circle cx="6" cy="9.6" r="0.7" fill="#fff"/>
        </svg>
      </p>
      <p class="contact__line">BrightNestMums.example
        <svg class="contact__icon" viewBox="0 0 12 12" aria-hidden="true">
          <circle cx="6" cy="6" r="5.5" fill="#fff"/>
          <path d="M3,3.5 C4.5,4 4,6 5.5,6.5 C6.5,7 5.5,9 6.5,10 M7.5,1.8 C8,3 9.5,3 10,4.5" fill="none" stroke="var(--brand-wave)" stroke-width="1.1"/>
        </svg>
      </p>
      <p class="contact__address">47 Kowhai Terrace, Ellerslie<br>Auckland 1051, New Zealand</p>
    </div>
  </section>

  <section class="card card--back">
    <div class="back-mark">
      <span class="back-mark__dot"></span>
      <span class="back-mark__name">BrightNestMums</span>
    </div>
    <p class="strapline">Tap; Gather; Sorted</p>
  </section>

</body>
</html>
```